Enrollment Campaign

We need a flyer design for our school's enrollment campaign. Our school website is www.tbvacademy.net.

The flyer should be double sided.

I want the reader to get the following messages:
1. Montessori graduates are leading the top companies of our time.
2. We are an accredited Montessori school.
3. Enrollment is open now for all four programs:
a) Toddler: 18months (or as soon as the child is able to walk) - 3 years
b) CASA: Preschool to Senior Kindergarten (3 years to 6 years)
c) Elementary: Grades 1 to 6
d) Junior High: Grades 7 to 8
4) Our contact information:
website, email:info@tbvacademy.net, phone: 647 382 5146
5) Call for Action: Book a Tour! (there is a button on our website to book a tour)
6) In the languages punjabi, hindi and italian, I wouldn't readers to know that we offer their faith and cultural education as well.
7) Fees for children under age of 6 can be claimed in Taxes as day care expense. So, there is no reason to miss providing our children the best that we can in education.
Updates

Please note my updates to my brief in the "must have" section. Also, I have added some pics that can be used. Please note that I don't have one pic (the farming one referred to in my brief). I will really appreciate if you can kindly update your design accordingly.

Reason: Because of my recent update to the brief, some designers need some time to adjust their designs. I really appreciate your patience and kind consideration for my project. Thank you!

Industry/Entity Type

Education

Colors

Designer to choose colors to be used in the design.

Requirements
Must have
• Must have a unique design. I don't want a typical flyer. The design should be unique and memorable.

One of the main pics that I need is for illustrating a key feature of our new Junior High program that we are starting in August 2015. The key feature is that children are going to be operating a 'greenhouse', growing organic produce and will also be preparing their daily lunch from scratch. So, show a pic of a 13-14year old farming or something.

```html
<!DOCTYPE html>
<html lang="en">
<head>
<meta charset="utf-8">
<title>TBV Academy – Enrollment Flyer</title>
<link rel="stylesheet" href="https://fonts.googleapis.com/css2?family=Ubuntu:wght@400;500;700&family=Lato:wght@400;700;900&display=swap">
<style>
  :root{
    --stage:#acacac;
    --white:#ffffff;
    --sky-top:#38b4e8;
    --sky-mid:#6fdcef;
    --sky-low:#aef0e6;
    --grass:#7fd12a;
    --grass-light:#c6f26a;
    --grass-deep:#3fae1e;
    --leaf:#9fe04a;
    --headline:#e8262c;
    --brand-blue:#2ba3d8;
    --slogan-green:#6cc41c;
    --band-blue:#1d6fd1;
    --burst-outer:#e8321d;
    --burst-inner:#ffb400;
    --label:#3d5a3a;
    --cta-yellow:#fff23a;
    --contact-green:#2b6b12;
    --ring-orange:#f07c16;
    --ring-red:#e0231c;
    --ring-blue:#1438a8;
    --ring-cyan:#2fb7e6;
  }
  *{margin:0;padding:0;box-sizing:border-box}
  html,body{width:1200px;height:1000px;overflow:hidden;background:var(--stage)}
  body{position:relative;font-family:"Lato",sans-serif}
  .page{position:absolute;top:122px;width:476px;height:708px;overflow:hidden}
  .page--front{left:112px}
  .page--back{left:600px}
  .page svg.backdrop{position:absolute;inset:0}
  .abs{position:absolute}

  .brand{left:36px;top:40px;font-family:"Ubuntu",sans-serif;font-size:21px;font-weight:400;color:var(--brand-blue)}
  .slogan{left:182px;top:46px;font-family:"Ubuntu",sans-serif;font-size:15px;font-weight:500;color:var(--slogan-green)}
  .headline{font-family:"Ubuntu",sans-serif;font-weight:700;color:var(--headline);line-height:1.18}
  .headline--front{left:38px;top:144px;font-size:30px}
  .burst-text{left:320px;top:214px;width:140px;text-align:center;font-family:"Ubuntu",sans-serif;font-weight:700;font-size:20px;color:var(--white);line-height:1.05;transform:rotate(-14deg);text-shadow:1px 1px 0 #8a1e0c,-1px -1px 0 #8a1e0c,1px -1px 0 #8a1e0c,-1px 1px 0 #8a1e0c}
  .cta{left:20px;top:665px;font-size:11px;font-weight:700;color:var(--cta-yellow)}
  .cta strong{font-size:14px}
  .front-url{right:18px;top:684px;font-size:11px;font-weight:700;color:var(--white)}

  .headline--back{left:198px;top:28px;width:260px;font-size:22px;line-height:1.38}
  .program{text-align:center;color:var(--label);font-size:11px;line-height:1.3}
  .program b{display:block;font-size:13px;font-weight:700;letter-spacing:.3px}
  .program--toddler{left:70px;top:283px;width:180px}
  .program--elementary{left:300px;top:270px;width:130px}
  .program--casa{left:226px;top:461px;width:180px}
  .program--junior{left:58px;top:504px;width:140px}
  .faith-note{left:38px;top:566px;width:410px;font-size:12px;color:#4f6330;line-height:1.5}
  .fee-note{left:24px;top:654px;width:230px;font-size:10px;color:#777;line-height:1.4}
  .contact{right:26px;top:624px;text-align:right;font-size:14px;font-weight:700;color:var(--contact-green);line-height:24px}
</style>
</head>
<body>

<section class="page page--front">
  <svg class="backdrop" width="476" height="708" viewBox="0 0 476 708">
    <defs>
      <linearGradient id="frontSky" x1="0" y1="0" x2="0" y2="1">
        <stop offset="0" stop-color="var(--sky-top)"/>
        <stop offset=".45" stop-color="var(--sky-mid)"/>
        <stop offset="1" stop-color="var(--sky-low)"/>
      </linearGradient>
      <linearGradient id="frontGrass" x1="0" y1="0" x2="0" y2="1">
        <stop offset="0" stop-color="var(--grass-light)"/>
        <stop offset="1" stop-color="var(--grass-deep)"/>
      </linearGradient>
      <radialGradient id="leafGlow">
        <stop offset="0" stop-color="var(--leaf)" stop-opacity=".95"/>
        <stop offset=".7" stop-color="var(--grass)" stop-opacity=".6"/>
        <stop offset="1" stop-color="var(--grass)" stop-opacity="0"/>
      </radialGradient>
      <radialGradient id="softLight">
        <stop offset="0" stop-color="#ffffff" stop-opacity=".75"/>
        <stop offset="1" stop-color="#ffffff" stop-opacity="0"/>
      </radialGradient>
      <linearGradient id="kidsTone" x1="0" y1="0" x2="0" y2="1">
        <stop offset="0" stop-color="#e9a3c8"/>
        <stop offset=".5" stop-color="#e6b48e"/>
        <stop offset="1" stop-color="#6fc24a"/>
      </linearGradient>
    </defs>
    <rect width="476" height="708" fill="url(#frontSky)"/>
    <ellipse cx="240" cy="140" rx="260" ry="60" fill="url(#softLight)" role="img" aria-label="Soft white clouds"/>
    <ellipse cx="230" cy="420" rx="230" ry="140" fill="url(#softLight)" opacity=".7" role="img" aria-label="Sparkles and floating bubbles"/>
    <polygon points="0,0 476,0 476,82 0,100" fill="var(--white)"/>
    <polygon points="0,100 476,82 476,88 0,106" fill="var(--band-blue)"/>
    <path d="M0,630 C120,575 300,575 476,610 L476,708 L0,708 Z" fill="url(#frontGrass)"/>
    <rect y="658" width="476" height="50" fill="var(--grass-deep)"/>
    <ellipse cx="40" cy="560" rx="80" ry="120" fill="url(#leafGlow)" role="img" aria-label="Illustrated leafy branch on the left"/>
    <ellipse cx="420" cy="560" rx="90" ry="150" fill="url(#leafGlow)" role="img" aria-label="Illustrated leafy branch on the right"/>
    <ellipse cx="238" cy="690" rx="220" ry="30" fill="url(#leafGlow)" opacity=".8" role="img" aria-label="Small leaves along the bottom edge"/>
    <path d="M175,298 C230,290 250,310 262,360 C300,380 300,470 310,540 C320,580 310,610 300,624 L100,624 C90,590 94,520 120,470 C130,420 150,400 160,360 C162,320 165,302 175,298 Z"
          fill="url(#kidsTone)" opacity=".9" role="img" aria-label="Photo of five smiling children stacked in a playful pyramid on the grass"/>
    <polygon points="464,240 442,254 454,277 428,278 427,304 404,292 390,314 376,292 353,304 352,278 326,277 338,254 316,240 338,226 326,203 352,202 353,176 376,188 390,166 404,188 427,176 428,202 454,203 442,226"
             fill="var(--burst-outer)"/>
    <polygon transform="translate(390 240) scale(.82) translate(-390 -240)"
             points="464,240 442,254 454,277 428,278 427,304 404,292 390,314 376,292 353,304 352,278 326,277 338,254 316,240 338,226 326,203 352,202 353,176 376,188 390,166 404,188 427,176 428,202 454,203 442,226"
             fill="var(--burst-inner)"/>
  </svg>
  <div class="abs brand">TBV Academy</div>
  <div class="abs slogan">Free the learning spirit</div>
  <h1 class="abs headline headline--front">An accredited<br>Montessori School</h1>
  <div class="abs burst-text">Enrollment<br>Open</div>
  <p class="abs cta">Call for Action: <strong>Book a Tour !</strong> (there is a button on our website to book a tour)</p>
  <p class="abs front-url">www.tbvacademy.net</p>
</section>

<section class="page page--back">
  <svg class="backdrop" width="476" height="708" viewBox="0 0 476 708">
    <defs>
      <linearGradient id="backSky" x1="0" y1="0" x2="0" y2="1">
        <stop offset="0" stop-color="var(--sky-top)"/>
        <stop offset=".5" stop-color="var(--sky-mid)"/>
        <stop offset="1" stop-color="var(--sky-low)"/>
      </linearGradient>
      <radialGradient id="backLeaf">
        <stop offset="0" stop-color="var(--leaf)" stop-opacity=".95"/>
        <stop offset=".7" stop-color="var(--grass)" stop-opacity=".55"/>
        <stop offset="1" stop-color="var(--grass)" stop-opacity="0"/>
      </radialGradient>
      <radialGradient id="backLight">
        <stop offset="0" stop-color="#ffffff" stop-opacity=".8"/>
        <stop offset="1" stop-color="#ffffff" stop-opacity="0"/>
      </radialGradient>
    </defs>
    <rect width="476" height="708" fill="url(#backSky)"/>
    <ellipse cx="330" cy="110" rx="200" ry="70" fill="url(#backLight)" role="img" aria-label="Soft white clouds"/>
    <ellipse cx="400" cy="330" rx="140" ry="110" fill="url(#backLight)" opacity=".8" role="img" aria-label="Swirling white light streaks"/>
    <ellipse cx="50" cy="60" rx="130" ry="110" fill="url(#backLeaf)" role="img" aria-label="Illustrated green leaves hanging from a branch"/>
    <ellipse cx="60" cy="480" rx="120" ry="80" fill="url(#backLeaf)" opacity=".8" role="img" aria-label="Illustrated bright green leaves on the left"/>
    <ellipse cx="400" cy="470" rx="120" ry="90" fill="url(#backLeaf)" opacity=".8" role="img" aria-label="Illustrated bright green leaves on the right"/>
    <path d="M0,540 C140,520 300,560 476,520 L476,620 C330,650 150,600 0,640 Z" fill="var(--grass)"/>
    <path d="M0,600 C150,570 320,630 476,600 L476,625 C320,660 150,600 0,625 Z" fill="var(--grass-deep)"/>
    <path d="M0,625 C150,600 320,660 476,625 L476,708 L0,708 Z" fill="var(--white)"/>
    <circle cx="162" cy="206" r="66" fill="#9a6a48" stroke="var(--ring-orange)" stroke-width="7" role="img" aria-label="Photo of a toddler working with wooden materials"/>
    <circle cx="366" cy="198" r="58" fill="#c8a88a" stroke="var(--ring-red)" stroke-width="6" role="img" aria-label="Photo of an elementary child arranging counting beads on the floor"/>
    <circle cx="316" cy="378" r="66" fill="#b48a6a" stroke="var(--ring-cyan)" stroke-width="7" role="img" aria-label="Photo of preschool children sharing a snack at a table"/>
    <circle cx="128" cy="418" r="68" fill="#8a7560" stroke="var(--ring-blue)" stroke-width="7" role="img" aria-label="Photo of a junior high student working with a teacher"/>
  </svg>
  <h2 class="abs headline headline--back">Montessori graduates<br>are leading the top<br>companies of our time</h2>
  <div class="abs program program--toddler"><b>TODDLER</b>18 months (or as soon as the<br>child is able to walk) - 3 years</div>
  <div class="abs program program--elementary"><b>ELEMENTARY</b>Grades 1 to 6</div>
  <div class="abs program program--casa"><b>CASA</b>Preschool to Senior Kindergarten<br>(3 years to 6 years)</div>
  <div class="abs program program--junior"><b>JUNIOR HIGH</b>Grades 7 to 8</div>
  <p class="abs faith-note">We also offer faith and cultural education in Punjabi, Hindi and Italian, so your child keeps close to home.</p>
  <p class="abs fee-note">Fees for children under 6 can be claimed as day care expense.</p>
  <div class="abs contact">www.tbvacademy.net<br>info@tbvacademy.net<br>647 382 5146</div>
</section>

</body>
</html>
```